Kitchen and custom cabinetry company looking for business card design

We make: * Custom Kitchens, contemporary and traditional kitchens, Vanities, Libraries, Custom Entry Doors, Custom Wine Cellars and Custom Design Furniture. Phone number 555-284-7716. Address: Westhampton NY. Email: KAVRO@mailbox.example Portfolio at: KAVROcabinetry.example I would like moderns fonts and not heavy lines. double side but maybe will use clear plastic. I attached the logo.

Industry/Entity Type

Business

```html
<!DOCTYPE html>
<html lang="en">
<head>
<meta charset="utf-8">
<title>KAVRO Cabinetry Inc. – Business Card</title>
<link rel="stylesheet" href="https://fonts.googleapis.com/css2?family=Cinzel:wght@400;700&display=swap">
<style>
  :root {
    --orange: #f15a29;
    --orange-soft: #f47b53;
    --orange-pattern: #f36d40;
    --grey: #7d7d7d;
    --logo-grey: #6f6f6f;
    --white: #ffffff;
    --paper: #f8f8f8;
    --backdrop: #e9e5df;
  }
  * { box-sizing: border-box; margin: 0; padding: 0; }
  html, body { width: 1200px; height: 970px; overflow: hidden; }
  body {
    background: var(--backdrop);
    position: relative;
    font-family: "Cinzel", serif;
  }
  .card {
    position: absolute;
    top: 136px;
    width: 409px;
    height: 715px;
    border-radius: 22px;
    overflow: hidden;
  }
  .card--front { left: 152px; background: var(--paper); }
  .card--back { left: 646px; background: var(--orange); }
  .card__art { position: absolute; inset: 0; width: 100%; height: 100%; }

  .top-stripes { position: absolute; top: 0; left: 0; right: 0; height: 28px; display: flex; }
  .top-stripes span { flex: 1; }
  .top-stripes .s-orange { background: var(--orange); }
  .top-stripes .s-grey { background: var(--grey); }

  .wordmark {
    position: absolute; left: 0; right: 0;
    display: flex; align-items: center; justify-content: center; gap: 10px;
    font-weight: 700; font-size: 22px; letter-spacing: 1px; line-height: 1;
    white-space: nowrap;
  }
  .wordmark__square { width: 14px; height: 14px; flex: none; }
  .card--front .wordmark { top: 120px; color: var(--logo-grey); }
  .card--front .wordmark__square { background: var(--orange); }
  .card--back .wordmark { top: 620px; color: var(--white); }
  .card--back .wordmark__square { background: var(--white); }

  .person { position: absolute; left: 44px; top: 408px; color: var(--white); }
  .person__name { font-weight: 700; font-size: 21px; letter-spacing: 0.5px; }
  .person__role { font-size: 15px; margin-top: 2px; }

  .contacts { position: absolute; left: 44px; top: 475px; list-style: none; color: var(--white); font-size: 14.5px; }
  .contacts li { display: flex; align-items: center; gap: 12px; height: 21px; white-space: nowrap; }
  .contacts svg { width: 16px; height: 16px; flex: none; }

  .services { position: absolute; left: 44px; top: 558px; list-style: none; color: var(--white); font-size: 13.5px; }
  .services li { height: 17px; display: flex; align-items: center; gap: 6px; white-space: nowrap; }
  .services li::before { content: ""; width: 5px; height: 5px; border-radius: 50%; background: var(--white); }
</style>
</head>
<body>

<section class="card card--front" aria-label="Business card front">
  <svg class="card__art" viewBox="0 0 409 715" aria-hidden="true">
    <defs>
      <linearGradient id="silver-front" x1="0" y1="0" x2="1" y2="0">
        <stop offset="0" stop-color="#ffffff"/>
        <stop offset="0.45" stop-color="#d9dde0"/>
        <stop offset="0.7" stop-color="#a9b2b8"/>
        <stop offset="1" stop-color="#eef1f2"/>
      </linearGradient>
    </defs>
    <path d="M0,255 Q170,340 409,150 L409,205 Q190,370 0,305 Z" fill="url(#silver-front)"/>
    <path d="M0,310 Q200,370 409,190 L409,715 L0,715 Z" fill="var(--orange-soft)"/>
    <path d="M0,355 Q230,345 409,240 L409,715 L0,715 Z" fill="var(--orange)"/>
  </svg>

  <div class="top-stripes">
    <span class="s-orange"></span><span class="s-grey"></span><span class="s-orange"></span><span class="s-grey"></span>
  </div>

  <div class="wordmark"><span class="wordmark__square"></span>KAVRO CABINETRY INC.</div>

  <div class="person">
    <p class="person__name">Dana Whitlow</p>
    <p class="person__role">Manager</p>
  </div>

  <ul class="contacts">
    <li>
      <svg viewBox="0 0 16 16"><path d="M2 6 Q8 1 14 6 L12 8 L10 6.5 L6 6.5 L4 8 Z M4 9 L12 9 L13 14 L3 14 Z" fill="#fff"/></svg>
      555-284-7716
    </li>
    <li>
      <svg viewBox="0 0 16 16"><rect x="1.5" y="3.5" width="13" height="9" fill="none" stroke="#fff" stroke-width="1.4"/><path d="M1.5 3.5 L8 9 L14.5 3.5" fill="none" stroke="#fff" stroke-width="1.4"/></svg>
      KAVRO@mailbox.example
    </li>
    <li>
      <svg viewBox="0 0 16 16"><rect x="1.5" y="2.5" width="13" height="9" fill="none" stroke="#fff" stroke-width="1.4"/><path d="M6 14 L10 14 M8 11.5 L8 14" stroke="#fff" stroke-width="1.4"/></svg>
      www.KAVROcabinetry.example
    </li>
  </ul>

  <ul class="services">
    <li>Custom Kitchens</li>
    <li>contemporary kitchens</li>
    <li>traditional kitchens</li>
    <li>Vanities</li>
    <li>Libraries</li>
    <li>Custom Entry Doors</li>
    <li>Custom Wine Cellars</li>
    <li>Custom Design Furniture.</li>
  </ul>
</section>

<section class="card card--back" aria-label="Business card back">
  <svg class="card__art" viewBox="0 0 409 715">
    <defs>
      <linearGradient id="silver-back" x1="0" y1="0" x2="1" y2="0">
        <stop offset="0" stop-color="#e6e9eb"/>
        <stop offset="0.5" stop-color="#b3bcc2"/>
        <stop offset="1" stop-color="#f4f6f7"/>
      </linearGradient>
    </defs>
    <rect width="409" height="715" fill="var(--orange-pattern)" role="img" aria-label="Repeating diamond pattern in orange tones"/>
    <path d="M0,160 Q150,300 409,265 L409,290 Q170,330 0,190 Z" fill="url(#silver-back)"/>
    <path d="M0,190 Q170,330 409,290 L409,350 Q200,400 0,270 Z" fill="#f58a63" opacity="0.7"/>
  </svg>

  <div class="wordmark"><span class="wordmark__square"></span>KAVRO CABINETRY INC.</div>
</section>

</body>
</html>
```